Business Cards for a law firm

Business cards for our law firm. Use our silhoette logo and OAK PARTNERS - check our website (www.oakpartners.example)

Contact Information for Business Card

our silhouette logo, OAK PARTNERS, 800-555-0147, Dorian Pemberton, dorian@oakpartners.example

Requirements
Must have
• our silhouette logo, OAK PARTNERS, 800-555-0147, Dorian Pemberton, dorian@oakpartners.example

```html
<!DOCTYPE html>
<html lang="en">
<head>
<meta charset="utf-8">
<title>Oak Partners – Business Cards</title>
<link rel="stylesheet" href="https://fonts.googleapis.com/css2?family=Montserrat:wght@400;700&display=swap">
<style>
  :root {
    --backdrop: #e3e7e9;
    --navy: #22336a;
    --navy-soft: #2b3f7c;
    --sky: #3a7cc8;
    --white: #ffffff;
  }
  * { margin: 0; padding: 0; box-sizing: border-box; }
  html, body { width: 1200px; height: 960px; overflow: hidden; }
  body {
    position: relative;
    background: var(--backdrop);
    font-family: "Montserrat", Arial, sans-serif;
  }
  .card {
    position: absolute;
    left: 250px;
    width: 701px;
    height: 400px;
    background: var(--navy);
    overflow: hidden;
  }
  .card--front { top: 60px; }
  .card--back { top: 500px; }

  .wordmark {
    position: absolute;
    display: flex;
    align-items: center;
    gap: 18px;
  }
  .wordmark__mark { flex: none; }
  .wordmark__name {
    font-weight: 400;
    text-transform: uppercase;
    line-height: 0.92;
    letter-spacing: 0.02em;
  }
  .card--front .wordmark { left: 380px; top: 0; left: 115px; top: 140px; }
  .card--front .wordmark__mark { width: 70px; height: 70px; background: var(--sky); }
  .card--front .wordmark__name { color: var(--sky); font-size: 52px; }

  .card--back .wordmark { left: 20px; top: 38px; }
  .card--back .wordmark__mark { width: 60px; height: 60px; background: var(--white); }
  .card--back .wordmark__name { color: var(--white); font-size: 38px; }

  .figure-panel {
    position: absolute;
    right: 0;
    top: 0;
    width: 268px;
    height: 400px;
    background: linear-gradient(90deg, var(--navy-soft) 0%, var(--navy) 55%, var(--white) 100%);
  }

  .holder {
    position: absolute;
    left: 0;
    top: 247px;
    display: flex;
    align-items: center;
  }
  .holder__bar { width: 13px; height: 28px; background: var(--white); margin-right: 13px; }
  .holder__name {
    color: var(--white);
    font-size: 27px;
    letter-spacing: 0.04em;
    font-weight: 400;
    text-transform: uppercase;
  }
  .holder__name strong { font-weight: 700; }

  .contacts {
    position: absolute;
    left: 24px;
    top: 309px;
    list-style: none;
  }
  .contacts__item {
    display: flex;
    align-items: center;
    height: 23px;
    color: var(--white);
    font-size: 15px;
    letter-spacing: 0.08em;
    text-transform: uppercase;
  }
  .contacts__item svg { width: 15px; height: 15px; margin-right: 11px; flex: none; }
</style>
</head>
<body>
  <section class="card card--front" aria-label="Card front">
    <div class="wordmark">
      <span class="wordmark__mark"></span>
      <span class="wordmark__name">Oak<br>Partners</span>
    </div>
  </section>

  <section class="card card--back" aria-label="Card back">
    <div class="wordmark">
      <span class="wordmark__mark"></span>
      <span class="wordmark__name">Oak<br>Partners</span>
    </div>

    <div class="figure-panel" role="img" aria-label="Large brand figures area"></div>

    <div class="holder">
      <span class="holder__bar"></span>
      <h1 class="holder__name"><strong>Dorian</strong> Pemberton</h1>
    </div>

    <ul class="contacts">
      <li class="contacts__item">
        <svg viewBox="0 0 16 16" aria-hidden="true"><path d="M3 1.5l3 .5 1 3-1.7 1.3a9 9 0 0 0 4.4 4.4L11 9l3 1 .5 3-1.5 1.5C7 14.5 1.5 9 1.5 3z" fill="none" stroke="#fff" stroke-width="1.4" stroke-linejoin="round"/></svg>
        800-555-0147
      </li>
      <li class="contacts__item">
        <svg viewBox="0 0 16 16" aria-hidden="true"><circle cx="8" cy="8" r="6.5" fill="none" stroke="#fff" stroke-width="1.4"/><path d="M1.5 8h13M8 1.5c2.2 2 2.2 11 0 13M8 1.5c-2.2 2-2.2 11 0 13" fill="none" stroke="#fff" stroke-width="1.1"/></svg>
        www.oakpartners.example
      </li>
      <li class="contacts__item">
        <svg viewBox="0 0 16 16" aria-hidden="true"><rect x="1.5" y="3.5" width="13" height="9" fill="none" stroke="#fff" stroke-width="1.4"/><path d="M1.5 3.5L8 9l6.5-5.5" fill="none" stroke="#fff" stroke-width="1.4"/></svg>
        dorian@oakpartners.example
      </li>
    </ul>
  </section>
</body>
</html>
```